Kelvaro.ch is looking for business card letterhead and envelope C5 with WOW effect

We need a strong business card for our company Kelvaro.ch, logo is available. You want a black or dark background on which the logo Stark r% 26 # 252; appears. Letterhead and envelope in C5 format should be in a similar design, but does not have to be We need a strong business card for our company Kelvaro.ch, logo is available. A black or dark background is desired, on which the logo Stark comes across. The letterhead and the envelope in C5 format should have a similar design.

Target Market(s)

Private customers as well as entrepreneurs

Contact Information for Business Card

E-mail: info@kelvaro-example.ch
Web.www.Kelvaro-example.ch
Tel: +41 ( 0 ) 79 482 6037
Adresse:
Lindenweg 14
9406 Tarnbach

Hier kann man Icons verwenden für Email,Tel und Adressse

Font styles to use
Other font styles liked:
• Dubai,bold

Colors

Designer to choose colors to be used in the design.

Requirements
Must have
• WOW effect
Nice to have
• R% 26 # 252; back business card with our service listings. - VEHICLE LABELING - SHOP WINDOW LABELING - STICKERS AND MUCH MORE ... in red color

```html
<!DOCTYPE html>
<html lang="en">
<head>
<meta charset="utf-8">
<title>Kelvaro.ch – Business Card</title>
<link href="https://fonts.googleapis.com/css2?family=Arimo:wght@400&family=Mulish:wght@700;800&display=swap" rel="stylesheet">
<style>
  :root {
    --stage: #c9c9c9;
    --card-black: #0a0a0a;
    --brand-yellow: #fccb1e;
    --text-white: #f2f2f2;
    --pattern-white: #f4f4f4;
  }
  * { margin: 0; padding: 0; box-sizing: border-box; }
  html, body {
    width: 1200px; height: 802px; overflow: hidden;
    background: var(--stage);
  }
  .stage { position: relative; width: 1200px; height: 802px; }
  .card {
    position: absolute; top: 274px;
    width: 443px; height: 264px;
    background: var(--card-black);
    overflow: hidden;
  }
  .card--front { left: 136px; }
  .card--back { left: 624px; }

  .brand-name {
    font-family: "Mulish", sans-serif;
    font-weight: 800;
    letter-spacing: 0.5px;
    text-transform: uppercase;
    white-space: nowrap;
  }
  .card--front .brand-name {
    position: absolute; left: 24px; top: 46px;
    font-size: 27px; color: var(--brand-yellow);
  }

  .contact-list {
    position: absolute; left: 24px; top: 140px;
    list-style: none;
    font-family: "Arimo", sans-serif;
    font-size: 13px; color: var(--text-white);
  }
  .contact-list li {
    display: flex; align-items: center; gap: 6px;
    height: 18px;
  }
  .contact-list svg { width: 15px; height: 15px; flex: none; }
  .contact-address {
    position: absolute; left: 26px; top: 213px;
    font-family: "Arimo", sans-serif;
    font-size: 13px; color: var(--text-white);
  }

  .honeycomb-area {
    position: absolute; left: 222px; top: 0;
    width: 221px; height: 264px;
    background: linear-gradient(90deg, var(--card-black) 0%, var(--pattern-white) 28%, var(--brand-yellow) 58%, var(--brand-yellow) 100%);
  }

  .back-brand {
    position: absolute; left: 0; right: 0; top: 92px;
    display: flex; justify-content: center; align-items: center; gap: 14px;
  }
  .brand-mark {
    width: 40px; height: 40px; background: var(--brand-yellow);
  }
  .card--back .brand-name {
    font-size: 28px; color: var(--text-white);
  }
  .service-list {
    position: absolute; left: 0; right: 0; top: 214px;
    text-align: center;
    font-family: "Mulish", sans-serif; font-weight: 700;
    font-size: 11px; line-height: 14px;
    color: var(--brand-yellow);
  }
</style>
</head>
<body>
<main class="stage">

  <section class="card card--front" aria-label="Business card front">
    <div class="brand-name">Kelvaro.ch</div>

    <ul class="contact-list">
      <li>
        <svg viewBox="0 0 16 16" aria-hidden="true">
          <rect x="1" y="1" width="14" height="14" rx="2" fill="none" stroke="var(--brand-yellow)" stroke-width="1.4"/>
          <path d="M5 4.2c.6-.4 1.2-.2 1.5.4l.6 1.2c.2.4 0 .8-.3 1.1l-.4.3c.5 1 1.2 1.8 2.2 2.3l.3-.4c.3-.3.7-.4 1.1-.2l1.2.6c.6.3.7 1 .3 1.5-.6.8-1.6 1-2.5.6C7.2 10.7 5.7 9.2 4.8 7.4c-.4-.9-.3-2.4.2-3.2z" fill="var(--brand-yellow)"/>
        </svg>
        <span>+41 ( 0 ) 79 482 6037</span>
      </li>
      <li>
        <svg viewBox="0 0 16 16" aria-hidden="true">
          <rect x="0.5" y="3" width="15" height="10" fill="var(--brand-yellow)"/>
          <path d="M0.5 3.5L8 9l7.5-5.5M0.5 12.5L6 8M15.5 12.5L10 8" fill="none" stroke="var(--card-black)" stroke-width="1"/>
        </svg>
        <span>info@kelvaro-example.ch</span>
      </li>
      <li>
        <svg viewBox="0 0 16 16" aria-hidden="true">
          <g fill="none" stroke="var(--brand-yellow)" stroke-width="1.3">
            <circle cx="8" cy="8" r="7"/>
            <ellipse cx="8" cy="8" rx="3" ry="7"/>
            <path d="M1 8h14M2 4.5h12M2 11.5h12"/>
          </g>
        </svg>
        <span>www.Kelvaro-example.ch</span>
      </li>
    </ul>

    <p class="contact-address">Lindenweg 14,9406 Tarnbach</p>

    <div class="honeycomb-area" role="img" aria-label="Honeycomb pattern of white and yellow hexagons fading into a yellow panel"></div>
  </section>

  <section class="card card--back" aria-label="Business card back">
    <div class="back-brand">
      <span class="brand-mark" aria-hidden="true"></span>
      <span class="brand-name">Kelvaro.ch</span>
    </div>
    <p class="service-list">
      VEHICLE LABELING | SHOP WINDOW LABELING<br>
      STICKERS AND MUCH MORE ...
    </p>
  </section>

</main>
</body>
</html>
```